Web Page Design for Major Airline Consolidator

We need a new design for an airline consolidator based out of NY. We'd really like to get the design as quickly as possible.

Here is a *very* rough mockup of what the site could look like, along with 3 main competitor's sites. Needless to say, they want a design that looks much better than their competitors. Please note that the mockup is an idea only, feel free to enhance / improve upon it.

Mockup - https://plankrafe.com/tvorel/KQPMzaLu

Competitors:
- http://www.brellintour.com/
- http://www.skorvatix.com/home2.html
- https://www.dulmerok.com/index.php

Target Market(s)

target markets are identified in the mockup

Industry/Entity Type

Airline

Number of Pages Required

1 page

Requirements
Must have
• need space on the left side for a travel request form which is missing in the mockup. Form should have standard air booking fields (to, from, date arrival & departure, travel class, etc).

```html
<!DOCTYPE html>
<html lang="en">
<head>
<meta charset="utf-8">
<title>Halvern Tours — Airline Consolidator</title>
<link href="https://fonts.googleapis.com/css2?family=Open+Sans:ital,wght@0,400;0,600;0,700;1,400;1,600&display=swap" rel="stylesheet">
<style>
:root{
  --blue:#3a72b8;
  --blue-dark:#2a5a98;
  --blue-light:#6fa3dc;
  --orange:#e8662b;
  --green:#6aa84f;
  --text:#444;
  --muted:#777;
  --line:#dcdcdc;
  --grey-bg:#e9e9e9;
  --white:#fff;
}
*{box-sizing:border-box;margin:0;padding:0}
html,body{width:1200px;height:3900px;overflow:hidden}
body{font-family:"Open Sans",Arial,sans-serif;color:var(--text);background:var(--white);position:relative;font-size:15px}
.section{position:absolute;left:0;width:1200px}
.abs{position:absolute}
.btn{display:inline-block;background:var(--blue);color:var(--white);font-weight:600;font-size:15px;text-align:center;padding:8px 0;border-radius:2px;text-transform:uppercase;white-space:nowrap}
.section-title{position:absolute;left:0;width:1200px;text-align:center;font-size:22px;font-weight:600;color:#333;text-transform:uppercase;letter-spacing:.5px}

/* header */
.site-header{top:0;height:56px}
.brand{left:40px;top:6px;display:flex;align-items:center;gap:10px}
.brand-dot{width:34px;height:34px;border-radius:50%;background:var(--blue)}
.brand-name{font-size:24px;font-weight:700;color:var(--blue);line-height:1;white-space:nowrap}
.brand-tag{font-size:10px;color:var(--muted);margin-top:3px;white-space:nowrap}
.account-links{right:40px;top:12px;display:flex;gap:6px}
.account-links span{border:1px solid var(--line);font-size:11px;font-weight:600;padding:4px 14px;color:#555}
.main-nav{top:56px;height:24px;border-top:1px solid var(--line);border-bottom:1px solid var(--line);display:flex;padding-left:40px}
.main-nav span{font-size:11px;font-weight:600;color:var(--blue);padding:4px 16px;text-transform:uppercase;white-space:nowrap}
.main-nav .active{background:var(--blue);color:var(--white)}

/* hero */
.hero{top:80px;height:740px;background:linear-gradient(180deg,#5fa8dc 0%,#8fcbe9 30%,#4fc2cf 55%,#2aa6b4 70%,#e6d8b4 92%,#d9c79c 100%)}
.hero-banner{left:112px;top:32px;width:440px;height:48px;background:rgba(58,114,184,.85);color:var(--white);font-size:18px;font-weight:600;line-height:48px;text-align:center;text-transform:uppercase;white-space:nowrap;letter-spacing:0}
.hero-reviews{left:112px;top:90px;width:440px;text-align:center;color:var(--white);font-size:13px;white-space:nowrap}
.access-box{left:780px;top:32px;width:360px;height:196px;background:rgba(120,170,90,.55);padding:18px 20px}
.access-box .field{background:rgba(255,255,255,.9);height:36px;margin-bottom:12px;font-size:12px;color:#888;line-height:36px;padding-left:12px}
.access-box .go{background:var(--green);color:var(--white);font-weight:600;text-align:center;height:44px;line-height:44px;font-size:16px}
.hero-arrow{top:330px;width:20px;height:40px}
.flight-search{left:112px;top:240px;width:976px;height:352px;background:rgba(35,65,105,.78);padding:16px 28px}
.fs-title{text-align:center;color:var(--white);font-weight:600;font-size:17px;letter-spacing:1px;margin-bottom:12px}
.fs-row{display:flex;gap:12px;margin-bottom:14px;align-items:center}
.fs-field{background:var(--white);height:38px;font-size:12px;color:#888;line-height:38px;padding-left:10px;position:relative;white-space:nowrap}
.fs-field.sel::after{content:"";position:absolute;right:10px;top:16px;border:5px solid transparent;border-top-color:#888}
.fs-opt{color:var(--white);font-size:12px;display:flex;align-items:center;gap:6px;white-space:nowrap}
.fs-opt i{width:12px;height:12px;border-radius:50%;background:var(--white);display:inline-block}
.fs-opt i.sq{border-radius:1px}
.fs-search{background:var(--blue);color:var(--white);font-weight:700;text-align:center;height:42px;line-height:42px;width:180px}
.fs-adv{color:#cfe3ff;font-size:12px;text-align:right;margin-top:4px}
.hero-caption{left:0;top:620px;width:1200px;text-align:center;color:var(--white);font-size:22px;font-weight:600;text-transform:uppercase}
.hero-icon{width:110px;height:110px;border-radius:50%;background:var(--white);border:4px solid #d6e6f7;top:685px;display:flex;align-items:center;justify-content:center}

/* audience columns */
.audiences{top:820px;height:310px}
.audience{top:48px;width:300px;text-align:center}
.audience h3{color:var(--blue);font-size:16px;font-weight:700;text-transform:uppercase;white-space:nowrap}
.audience .sub{font-size:13px;margin:8px 0 6px}
.audience ul{list-style:none;text-align:left;font-size:12px;line-height:1.7;padding-left:40px}
.audience .more{font-size:12px;color:var(--blue);margin-top:4px}
.audience .btn{width:170px;margin-top:18px}

/* business */
.business{top:1130px;height:370px;border-top:1px solid var(--line)}
.business .tagline{top:78px;left:0;width:1200px;text-align:center;color:var(--orange);font-weight:600;font-size:16px;text-transform:uppercase}
.easy-list{left:90px;top:114px;width:780px}
.easy-item{display:flex;align-items:center;gap:14px;height:52px;font-size:16px;white-space:nowrap}
.easy-item b{width:34px;height:34px;border-radius:50%;background:var(--blue);color:var(--white);text-align:center;line-height:34px;font-size:16px;flex:none}
.business .btn{left:380px;top:325px;width:400px}
.agent-photo{left:880px;top:40px;width:260px;height:300px;border-radius:130px 130px 0 0;background:linear-gradient(180deg,#f2f4f7,#d9e2ec)}

/* welcome */
.welcome{top:1500px;height:250px;border-top:1px solid var(--line)}
.welcome p{left:120px;top:84px;width:960px;text-align:center;font-size:14px;line-height:1.7}
.welcome .btn{left:540px;top:172px;width:120px;font-size:12px}

/* quote */
.quote{top:1752px;height:400px;background:linear-gradient(180deg,#f1f1f1,#dcdcdc)}
.ceo-photo{left:80px;top:20px;width:260px;height:380px;background:linear-gradient(180deg,#c9ced6,#5e6f86 60%,#3c4758)}
.quote blockquote{left:400px;top:100px;width:720px;text-align:center;font-style:italic;font-size:28px;line-height:1.45;color:#333}
.quote .who{left:400px;top:270px;width:720px;text-align:center;font-size:14px}

/* divisions & employees */
.team{top:2152px;height:270px;border-bottom:1px solid var(--line)}
.team h4{font-size:18px;font-weight:600;text-transform:uppercase;color:#333;text-align:center}
.divisions{left:60px;top:36px;width:460px;font-size:13px;line-height:1.7}
.divisions .links{margin-top:6px;color:var(--blue)}
.divisions .more{text-align:right;color:var(--blue);margin-top:4px}
.team-rule{left:580px;top:30px;width:1px;height:220px;background:var(--line)}
.employees{left:620px;top:36px;width:540px}
.emp-row{display:flex;justify-content:center;gap:34px;margin-top:22px}
.emp{width:120px;text-align:center;font-size:12px;line-height:1.5}
.emp .pic{width:88px;height:88px;margin:0 auto 6px;background:linear-gradient(180deg,#d5dbe3,#8793a4)}
.emp .more{color:var(--blue)}
.see-all{font-size:12px;color:var(--blue)}

/* places */
.places{top:2422px;height:500px}
.place{top:98px;width:220px;text-align:center}
.place .img{width:220px;height:200px}
.place h5{font-size:15px;font-weight:700;margin-top:14px;color:#333}
.place p{font-size:12px;line-height:1.5;margin-top:4px;color:var(--muted)}
.place .price{color:var(--orange);font-weight:700;font-size:15px;margin-top:4px}
.place .btn{width:220px;margin-top:10px;font-size:13px}
.car-arrow{top:190px;width:28px;height:28px;border-radius:50%;background:var(--blue)}

/* group travel */
.group{top:2922px;height:620px;border-top:1px solid var(--line)}
.group-card{top:118px;width:360px;text-align:center}
.group-card .img{width:360px;height:270px}
.group-card h5{font-size:16px;font-weight:700;margin-top:18px;text-transform:uppercase;color:#333}
.group-card p{font-size:12px;line-height:1.6;margin-top:6px;color:var(--muted)}
.group-card .btn{width:200px;margin-top:18px;font-size:13px}

/* trusted */
.trusted{top:3542px;height:208px}
.trusted .section-title{top:28px;font-size:18px}
.badge{top:100px;background:#9fb6d3}

/* footer */
.site-footer{top:3750px;height:150px;background:var(--blue)}
.site-footer .brand-name{color:var(--white)}
.site-footer .brand-dot{background:var(--white)}
.footer-contact{left:470px;top:34px;color:var(--white);font-size:12px;line-height:1.9}
.footer-contact div{display:flex;align-items:center;gap:8px;white-space:nowrap}
.footer-social{right:60px;top:48px;display:flex;gap:10px}
.footer-social i{width:30px;height:30px;border-radius:50%;background:rgba(255,255,255,.9);display:block}
.copyright{left:40px;top:124px;color:#dbe8f7;font-size:10px}
</style>
</head>
<body>

<header class="section site-header">
  <div class="abs brand">
    <div class="brand-dot"></div>
    <div><div class="brand-name">Halvern Tours</div><div class="brand-tag">Airline consolidator since 1981</div></div>
  </div>
  <div class="abs account-links"><span>SIGN IN</span><span>SIGN UP</span><span>MY ACCOUNT</span></div>
</header>
<nav class="section main-nav">
  <span class="active">Home</span><span>Travel Agencies</span><span>Religious Travel Group</span><span>Corporate Concierge</span><span>Niche Agencies</span><span>Destinations</span><span>About Halvern</span><span>Restricted Area</span>
</nav>

<section class="section hero" role="img" aria-label="Tropical beach with palm trees, turquoise sea and white sand">
  <div class="abs hero-banner">More than just airline consolidation</div>
  <div class="abs hero-reviews">Checkout Our Reviews ★★★★☆</div>
  <div class="abs access-box">
    <div class="field">Enter Your Name</div>
    <div class="field">Enter Your E-mail Address</div>
    <div class="go">Get Access Today!</div>
  </div>
  <svg class="abs hero-arrow" style="left:12px" viewBox="0 0 20 40"><path d="M16 4 4 20l12 16" fill="none" stroke="#fff" stroke-width="4"/></svg>
  <svg class="abs hero-arrow" style="left:1168px" viewBox="0 0 20 40"><path d="M4 4l12 16L4 36" fill="none" stroke="#fff" stroke-width="4"/></svg>

  <form class="abs flight-search">
    <div class="fs-title">FLIGHT SEARCH</div>
    <div class="fs-row">
      <div class="fs-field" style="width:230px">From (city or airport)</div>
      <div class="fs-field sel" style="width:150px">Depart Date</div>
      <div class="fs-field sel" style="width:110px">Anytime</div>
      <div class="fs-opt" style="width:90px"><i></i>Economy</div>
      <div class="fs-opt" style="width:120px"><i></i>First/Business</div>
      <div class="fs-opt"><i></i>Price</div>
    </div>
    <div class="fs-row">
      <div class="fs-field" style="width:230px">To (city or airport)</div>
      <div class="fs-field sel" style="width:150px">Return Date</div>
      <div class="fs-field sel" style="width:110px">Anytime</div>
      <div class="fs-opt" style="width:90px"><i></i>Schedule</div>
      <div class="fs-opt"><i></i>Nonstop/Direct</div>
    </div>
    <div class="fs-row">
      <div class="fs-field sel" style="width:109px">Adults 1</div>
      <div class="fs-field sel" style="width:109px">Children 0</div>
      <div class="fs-opt" style="width:100px"><i></i>Round trip</div>
      <div class="fs-opt" style="width:170px"><i class="sq"></i>Flexible +/- 3 days</div>
      <div class="fs-field" style="width:220px">Promo Code</div>
    </div>
    <div class="fs-row">
      <div class="fs-field sel" style="width:109px">Seniors 0</div>
      <div class="fs-field sel" style="width:109px">Infants 0</div>
      <div class="fs-opt" style="width:100px"><i></i>One way</div>
      <div class="fs-opt" style="width:170px"><i class="sq"></i>Search nearby airports</div>
      <div class="fs-opt" style="width:150px"><i></i>Multiple destinations</div>
      <div class="fs-search" style="margin-left:auto">SEARCH</div>
    </div>
    <div class="fs-adv">Advanced Search</div>
  </form>

  <div class="abs hero-caption">Airline consolidator for travel agents</div>
  <div class="abs hero-icon" style="left:185px">
    <svg width="56" height="56" viewBox="0 0 56 56" fill="none" stroke="#3a72b8" stroke-width="4"><path d="M6 28 28 8l22 20M13 23v25h30V23M23 48V34h10v14"/></svg>
  </div>
  <div class="abs hero-icon" style="left:545px">
    <svg width="60" height="56" viewBox="0 0 60 56" fill="none" stroke="#3a72b8" stroke-width="4"><circle cx="30" cy="16" r="8"/><path d="M16 48c0-10 6-16 14-16s14 6 14 16"/><circle cx="12" cy="22" r="5"/><circle cx="48" cy="22" r="5"/><path d="M2 44c0-7 4-11 10-11M58 44c0-7-4-11-10-11"/></svg>
  </div>
  <div class="abs hero-icon" style="left:905px">
    <svg width="56" height="56" viewBox="0 0 56 56" fill="none" stroke="#3a72b8" stroke-width="4"><path d="M12 50V8h22v42M34 22h12v28M6 50h44M19 16h8M19 26h8M19 36h8"/></svg>
  </div>
</section>

<section class="section audiences">
  <div class="abs audience" style="left:90px">
    <h3>Home based travel agents</h3>
    <p class="sub">Find your way to financial freedom!</p>
    <ul><li>• I don't have another client to the big guys</li><li>• I get more referrals and more customers</li></ul>
    <p class="more">learn more</p>
    <span class="btn">Join now</span>
  </div>
  <div class="abs audience" style="left:450px">
    <h3>Small travel agencies</h3>
    <p class="sub">Accelerate your growth!</p>
    <ul><li>• I don't lose another client to the big guys</li><li>• I get more referrals and more customers</li></ul>
    <p class="more">learn more</p>
    <span class="btn">Join now</span>
  </div>
  <div class="abs audience" style="left:810px">
    <h3>Corporate travel agencies</h3>
    <p class="sub">Earn &amp; retain higher value clients</p>
    <ul><li>• I don't lose another client to the big guys</li><li>• I get more referrals and more customers</li></ul>
    <p class="more">learn more</p>
    <span class="btn">Join now</span>
  </div>
</section>

<section class="section business">
  <h2 class="section-title" style="top:36px;font-size:20px">Airline consolidators for businesses &amp; corporations</h2>
  <p class="abs tagline">Tired of travel headaches? Make business travel easy!</p>
  <div class="abs easy-list">
    <div class="easy-item"><b>E</b>Excellent customer service, we staff over 200 agents and have locations in 6 major US cities</div>
    <div class="easy-item"><b>A</b>Always available ... buy in bulk &amp; save even more!</div>
    <div class="easy-item"><b>S</b>Save more by going direct to the consolidator!</div>
    <div class="easy-item"><b>Y</b>Your best interests are ours!</div>
  </div>
  <span class="abs btn">Experience the difference of Halvern</span>
  <div class="abs agent-photo" role="img" aria-label="Smiling customer service agent wearing a headset"></div>
</section>

<section class="section welcome">
  <h2 class="section-title" style="top:40px">Welcome</h2>
  <p class="abs">We're here for our clients. Over 40 years in business. Locations across the USA and a wide partner network. Worldwide, Europe &amp; Middle East travel. Excellent customer service, we staff over 200 agents and have locations in 6 major US cities. Always available ... buy in bulk &amp; save even more!</p>
  <span class="abs btn">Read more</span>
</section>

<section class="section quote">
  <div class="abs ceo-photo" role="img" aria-label="Company president in a suit with arms crossed"></div>
  <blockquote class="abs">"Great airfares are only the beginning, exceptional customer service and caring for our clients is what makes us so unique"</blockquote>
  <p class="abs who">Mr. Delcourt<br>President &amp; CEO</p>
</section>

<section class="section team">
  <div class="abs divisions">
    <h4>Our divisions</h4>
    <p style="margin-top:14px">Our team serves agencies, groups and corporate travelers with dedicated desks for every need, from airport services to cargo.</p>
    <p class="links">| The Airport / Airport Authority<br>| Air Cargo / Transfer</p>
    <p class="more">Read more</p>
  </div>
  <div class="abs team-rule"></div>
  <div class="abs employees">
    <h4>Our employees</h4>
    <div class="emp-row">
      <div class="emp"><div class="pic" role="img" aria-label="Employee portrait"></div>Tom Adler<br>Manager<br><span class="more">Read more</span></div>
      <div class="emp"><div class="pic" role="img" aria-label="Employee portrait"></div>Nina Brook<br>Agent<br><span class="more">Read more</span></div>
      <div class="emp"><div class="pic" role="img" aria-label="Employee portrait"></div>Sam Ortiz<br>Marketing Head<br><span class="more">Read more</span></div>
    </div>
  </div>
  <svg class="abs" style="left:610px;top:120px" width="14" height="24" viewBox="0 0 14 24"><path d="M11 2 3 12l8 10" fill="none" stroke="#999" stroke-width="3"/></svg>
  <svg class="abs" style="left:1150px;top:120px" width="14" height="24" viewBox="0 0 14 24"><path d="M3 2l8 10-8 10" fill="none" stroke="#999" stroke-width="3"/></svg>
  <span class="abs see-all" style="right:40px;top:236px">See all</span>
</section>

<section class="section places">
  <h2 class="section-title" style="top:36px">There are plenty of places that are worth seeing</h2>
  <svg class="abs car-arrow" style="left:80px" viewBox="0 0 28 28"><path d="M17 8l-6 6 6 6" fill="none" stroke="#fff" stroke-width="3"/></svg>
  <svg class="abs car-arrow" style="left:1092px" viewBox="0 0 28 28"><path d="M11 8l6 6-6 6" fill="none" stroke="#fff" stroke-width="3"/></svg>
  <div class="abs place" style="left:130px">
    <div class="img" role="img" aria-label="Resort pool beside the sea" style="background:linear-gradient(180deg,#7fb9e0,#3fa9b5 60%,#c9b58a)"></div>
    <h5>LOREM IPSUM</h5><p>Lorem ipsum dolor sit amet, consectetur adipiscing elit sed do.</p><p class="price">$ 500.00</p><span class="btn">Contact us now</span>
  </div>
  <div class="abs place" style="left:370px">
    <div class="img" role="img" aria-label="Ancient stone amphitheatre under blue sky" style="background:linear-gradient(180deg,#6fa7d8,#b79a74 55%,#8b7356)"></div>
    <h5>LOREM IPSUM</h5><p>Lorem ipsum dolor sit amet, consectetur adipiscing elit sed do.</p><p class="price">$ 500.00</p><span class="btn">Contact us now</span>
  </div>
  <div class="abs place" style="left:610px">
    <div class="img" role="img" aria-label="Mountain valley with green forest and lake" style="background:linear-gradient(180deg,#9cc4e4,#6e8a6a 50%,#3f6a4a)"></div>
    <h5>LOREM IPSUM</h5><p>Lorem ipsum dolor sit amet, consectetur adipiscing elit sed do.</p><p class="price">$ 500.00</p><span class="btn">Contact us now</span>
  </div>
  <div class="abs place" style="left:850px">
    <div class="img" role="img" aria-label="Tropical island with palm trees and lagoon" style="background:linear-gradient(180deg,#4e9bd6,#3cc0c8 55%,#3f8a55)"></div>
    <h5>LOREM IPSUM</h5><p>Lorem ipsum dolor sit amet, consectetur adipiscing elit sed do.</p><p class="price">$ 500.00</p><span class="btn">Contact us now</span>
  </div>
  <span class="abs see-all" style="right:80px;top:462px">See all</span>
</section>

<section class="section group">
  <h2 class="section-title" style="top:52px;font-size:20px">Group travel - missionary airfares, Hajj &amp; Umra discounted airfares</h2>
  <div class="abs group-card" style="left:192px">
    <div class="img" role="img" aria-label="Family group traveling together" style="background:linear-gradient(180deg,#cfd8cf,#8d9a7e 60%,#5c6a52)"></div>
    <h5>Hajj group travel rates</h5>
    <p>Lorem ipsum dolor sit amet, consectetur adipiscing elit. Nullam sed dui a mauris dictum lacinia in vel ante.</p>
    <span class="btn">Contact us now</span>
  </div>
  <div class="abs group-card" style="left:640px">
    <div class="img" role="img" aria-label="Missionary group posing outdoors" style="background:linear-gradient(180deg,#a9c9e6,#7aa36a 55%,#b8443c)"></div>
    <h5>Missionary travel</h5>
    <p>Lorem ipsum dolor sit amet, consectetur adipiscing elit. Nullam sed dui a mauris dictum lacinia in vel ante.</p>
    <span class="btn">Contact us now</span>
  </div>
</section>

<section class="section trusted">
  <h2 class="section-title">Trusted members of</h2>
  <div class="abs" style="left:300px;top:40px;width:150px;height:1px;background:var(--line)"></div>
  <div class="abs" style="left:750px;top:40px;width:150px;height:1px;background:var(--line)"></div>
  <div class="abs badge" style="left:330px;width:100px;height:90px;border-radius:50%"></div>
  <div class="abs badge" style="left:540px;width:120px;height:90px;border-radius:6px"></div>
  <div class="abs badge" style="left:770px;width:100px;height:90px;border-radius:50%"></div>
</section>

<footer class="section site-footer">
  <div class="abs brand" style="left:60px;top:40px">
    <div class="brand-dot"></div>
    <div><div class="brand-name">Halvern Tours</div><div class="brand-tag" style="color:#dbe8f7">Airline consolidator since 1981</div></div>
  </div>
  <div class="abs footer-contact">
    <div><svg width="12" height="14" viewBox="0 0 12 14"><path d="M6 13S1 8 1 5a5 5 0 0 1 10 0c0 3-5 8-5 8z" fill="#fff"/><circle cx="6" cy="5" r="2" fill="#3a72b8"/></svg>120 Harbor Lane, Suite 400, Brookvale NY 10020</div>
    <div><svg width="12" height="12" viewBox="0 0 12 12"><path d="M2 1h3l1 3-2 1a7 7 0 0 0 3 3l1-2 3 1v3c-6 0-10-4-10-9z" fill="#fff"/></svg>(555) 014-2290</div>
    <div><svg width="13" height="10" viewBox="0 0 13 10"><rect x="0.5" y="0.5" width="12" height="9" fill="none" stroke="#fff"/><path d="M1 1l5.5 4.5L12 1" fill="none" stroke="#fff"/></svg>info@halverntours.example</div>
  </div>
  <div class="abs footer-social"><i></i><i></i><i></i><i></i><i></i><i></i></div>
  <div class="abs copyright">© Halvern Tours. All rights reserved.</div>
</footer>

</body>
</html>
```